Verpackungsdesign für Pasta aus Buchweizen
Zielgruppe
Unser Unternehmen VELMORIA sucht ein sehr modernes Verpackungsdesign für Pasta aus Buchweizen.
Unsere Produkte sind in unserem Online Shop und unterscheiden sich durch die herkömmliche Pasta, da wir Buchweizen in die Verarbeitung mit aufnehmen und somit die gesundheitsfördernde Eigenschaft des Buchweizens im Vordergrund steht. Unsere Pasta aus Buchweizenmehl mit klassischem Hartweizengrieß ist in dieser Form noch nicht im stationären Handel erhältlich, deshalb wünschen wir uns ein neues, ansprechendes Verpackungsdesign welches von den Massenprodukten aus den Regalen im Handel heraussticht. Das Design sollte also minimalistisch und sehr modern wirken, und sich deutlich von der Konkurrenz abheben.
Die Zielgruppe richtet sich sowohl an Massen die Pasta in allen Variationen lieben, als auch an ernährungsbewusste Veganer/Vegetarier die Alternativen im Bereich der herkömmlichen Pasta Kochkultur suchen.
PS: Mit dem Verkauf unserer Pasta investieren wir außerdem in den Aufbau und der Infrastruktur des Erzeugerlandes. Durch unser Prinzip „Teilen & Wachsen“ fördern wir mit unseren Gewinnen nachhaltige Projekte in den Erzeugerländern und helfen somit wirtschaftlich benachteiligten Regionen auf der Welt. (Fair Trade)
Aufgabenstellung
Wir besitzen bereits ein Logo und Verpackungen für unsere Pasta Sorten. Das Logo und das Grundgerüst der Stanzform / Verpackungsmaße (inkl. Sichtfenster) soll beibehalten werden (Siehe Anhang). Als Pasta Verpackungen benutzen wir Faltschachteln und Banderolen.
Verpackungsmaße:
- Faltschachtel (90 x 40 x 165 mm)
- Banderole (560 x 70mm)
Der Produktname ist je nach Sorte zu präzisieren:
- Fusilli
- Makkaroni
- Bandnudeln
- Tarhana
Produktgewicht:
- 250g
Eigenschaften:
- Buchweizenmehl
- 100% Vegan
- Kochzeit 3 Minuten
- Liebevolle Handarbeit
WICHTIG:
1) Bitte benutzt die hochgeladene, leere Stanzform für Artwork.
2) Die Designfarbe kann anhand des Aufstellers ausgerichtet werden (CMYK: 0, 20, 32, 0 und 60, 57, 56, 62) es ist aber kein muss und ihr seit frei in der Kreativität.
3) Bitte das Sichtfenster mit Rand wie aktuell auf den Produkten übernehmen (siehe www.velmoria.de/shop)
Nach dem Wettbewerb planen wir zusätzlich ein 1zu1 Projekt und würden uns freuen einen Gewinner auszuwählen - Wir freuen uns auf eure Ideen :)

```html
<!DOCTYPE html>
<html lang="de">
<head>
<meta charset="utf-8">
<title>VELMORIA Makkaroni – Faltschachtel Frontansicht</title>
<link rel="stylesheet" href="https://fonts.googleapis.com/css2?family=Crimson+Text:wght@400;700&family=Roboto:wght@400;700&family=Roboto+Condensed:wght@400&display=swap">
<style>
  :root {
    --stage: #d9d9d9;
    --band-light: #fde3bd;
    --band-mid: #fbcb91;
    --band-deep: #e9b47f;
    --window-white: #f4f4f4;
    --window-cream: #fcfbdf;
    --frame: #fcd8b4;
    --ink: #9b6a48;
    --ink-soft: #a9805f;
    --pasta-light: #f0c47a;
    --pasta-deep: #c9924a;
    --blob: #fde0b6;
  }
  * { box-sizing: border-box; margin: 0; padding: 0; }
  html, body { width: 895px; height: 1200px; overflow: hidden; }
  body { background: var(--stage); position: relative; }

  .box-front {
    position: absolute;
    left: 267px;
    width: 360px;
    height: 560px;
    overflow: hidden;
    background: linear-gradient(120deg, var(--band-light), var(--band-mid) 60%, var(--band-deep));
  }
  .box-front--classic { top: 20px; }
  .box-front--spoon { top: 620px; }
  .box-front--spoon { background: linear-gradient(120deg, #fdf0d2, #fbe1b5 60%, #e8c89e); }

  .window {
    position: absolute;
    left: 0; right: 0;
    top: 82px;
    height: 390px;
    background: linear-gradient(100deg, #ffffff, var(--window-white) 70%, #e6e6e6);
  }
  .box-front--spoon .window { background: linear-gradient(100deg, #fffdf0, var(--window-cream)); }

  .window__frame {
    position: absolute;
    inset: 12px 8px 14px 8px;
    border: 3px solid var(--frame);
  }
  .window__frame::after {
    content: "";
    position: absolute;
    inset: 4px;
    border: 1px solid var(--frame);
  }

  .blob {
    position: absolute;
    left: 10px; top: 150px;
    width: 210px; height: 220px;
    border-radius: 50% 50% 10px 50%;
    background: var(--blob);
    opacity: .8;
  }

  .brand {
    position: absolute;
    left: 0; right: 0;
    top: 60px;
    display: flex;
    justify-content: center;
    align-items: center;
    gap: 8px;
    font-family: "Crimson Text", serif;
    font-weight: 700;
    font-size: 30px;
    letter-spacing: 1px;
    color: var(--ink);
  }
  .brand__dot {
    width: 12px; height: 12px;
    border-radius: 50%;
    background: var(--ink);
  }

  .product-name {
    position: absolute;
    right: 16px;
    top: 160px;
    font-family: "Crimson Text", serif;
    font-size: 33px;
    color: var(--ink);
  }
  .box-front--spoon .product-name {
    font-family: "Roboto", sans-serif;
    font-weight: 700;
    font-size: 28px;
    top: 168px;
  }

  .properties {
    position: absolute;
    left: 204px;
    top: 212px;
    font-family: "Crimson Text", serif;
    font-weight: 700;
    font-size: 13px;
    line-height: 19px;
    color: var(--ink-soft);
    list-style: none;
  }
  .box-front--spoon .properties { left: 192px; top: 218px; }

  .weight {
    position: absolute;
    right: 18px;
    bottom: 28px;
    font-family: "Roboto Condensed", sans-serif;
    font-size: 12px;
    color: var(--ink-soft);
  }

  .photo {
    position: absolute;
    border-radius: 40%;
    background: radial-gradient(circle at 45% 45%, var(--pasta-light), var(--pasta-deep));
  }
  .photo--penne { left: 10px; top: 185px; width: 200px; height: 185px; }
  .photo--spoon { left: 0; top: 178px; width: 180px; height: 110px; border-radius: 45% 40% 50% 30%;
    background: radial-gradient(circle at 60% 45%, #fbe27a, #e8b74a 80%, #c8c8c8); }
  .photo--penne-small { left: 8px; top: 292px; width: 130px; height: 100px; }
</style>
</head>
<body>

  <section class="box-front box-front--classic">
    <div class="window">
      <div class="blob"></div>
      <div class="window__frame"></div>
      <div class="brand"><span>VELMORIA</span><span class="brand__dot"></span></div>
      <h1 class="product-name">Makkaroni</h1>
      <ul class="properties">
        <li>Eigenschaften:</li>
        <li>- Buchweizenmehl</li>
        <li>- 100% Vegan</li>
        <li>- Kochzeit 3 Minuten</li>
        <li>- Liebevolle Handarbeit</li>
      </ul>
      <div class="photo photo--penne" role="img" aria-label="Foto: lose Penne-Nudeln aus Buchweizen"></div>
      <p class="weight">Produktgewicht: 250g</p>
    </div>
  </section>

  <section class="box-front box-front--spoon">
    <div class="window">
      <div class="window__frame"></div>
      <div class="brand"><span>VELMORIA</span><span class="brand__dot"></span></div>
      <h1 class="product-name">Makkaroni</h1>
      <ul class="properties">
        <li>Eigenschaften:</li>
        <li>- Buchweizenmehl</li>
        <li>- 100% Vegan</li>
        <li>- Kochzeit 3 Minuten</li>
        <li>- Liebevolle Handarbeit</li>
      </ul>
      <div class="photo photo--spoon" role="img" aria-label="Foto: Löffel mit gekochten Makkaroni"></div>
      <div class="photo photo--penne-small" role="img" aria-label="Foto: lose Penne-Nudeln aus Buchweizen"></div>
      <p class="weight">Produktgewicht: 250g</p>
    </div>
  </section>

</body>
</html>
```